Harbor Crest Holdings Corporate Showcase

Provide an attractive Corporate Website for a boutique Investment Company to showcase our activities and corporate interests.

Our Company works across a number of Sectors including

Real Estate
E-Commerce
Healthcare
Beauty & Personal Care
Technology
Resources

Lets keep the personality

Modern
Global
Sophisticated
Calm
Interesting

Lets keep the pages with MINIMAL Words
Lets use Photos/ Imagery to tell the story

We'll need a Banner Menu -
About Us
Expertise
Global Outlook
Sectors
Management
Media
Contact Us

Many thanks
Best wishes
Dennis.

Target Market(s)

Investors
Clients

Coding

Coded - Design and coding required

Number of Pages Required

5+ page

Font styles to use
Sans Serif

Colors
886aae
3176b5
00a990
f68e4d
f04a50
e667a6

Requirements
Must have
• WordPress Coding

Checkout this Website for look and feel - its cool:
www.qvr-example.com

Harbor Crest Partners
(Harbor Crest Holdings LLP)
London
E9 4ZX
United Kingdom

www.HarborCrestPartners-example.com
Nice to have
• Sophisticated colour palette - black/ brown/ blue/ purple/

```html
<!DOCTYPE html>
<html lang="en">
<head>
<meta charset="utf-8">
<title>Harbor Crest Holdings</title>
<link href="https://fonts.googleapis.com/css2?family=Montserrat:wght@300;400;500;600;700;800&display=swap" rel="stylesheet">
<style>
:root{
  --navy:#0b1634;
  --navy-2:#14285a;
  --purple:#886aae;
  --purple-band:#7656a3;
  --blue:#3176b5;
  --blue-bright:#2f6fc4;
  --green:#169d7d;
  --orange:#f68e4d;
  --red:#f04a50;
  --pink:#e667a6;
  --ink:#1d1d22;
  --body:#7a7a82;
  --line:#e2e4ea;
  --mist:#f1f3f7;
  --white:#ffffff;
}
*{box-sizing:border-box;margin:0;padding:0}
html,body{width:1200px;height:4946px;overflow:hidden}
body{font-family:"Montserrat",Arial,sans-serif;color:var(--ink);background:var(--white)}
.page{position:relative;width:1200px;height:4946px;overflow:hidden}
.abs{position:absolute}

/* hero */
.hero{position:absolute;left:0;top:0;width:1200px;height:640px;
  background:
   radial-gradient(ellipse 420px 300px at 760px 300px,rgba(52,110,200,.55),transparent 70%),
   radial-gradient(ellipse 300px 200px at 1050px 250px,rgba(200,40,90,.25),transparent 70%),
   linear-gradient(180deg,#0a1330 0%,#0f1f47 60%,#0b1736 100%)}
.hero__panel{position:absolute;left:265px;top:248px;width:670px;height:300px;background:rgba(5,10,28,.45)}
.brand{position:absolute;left:0;top:38px;width:1200px;text-align:center;color:var(--white);font-weight:700;font-size:27px;letter-spacing:.3px}
.nav{position:absolute;top:114px;left:0;width:1200px;height:20px}
.nav a{position:absolute;color:var(--white);font-size:12.5px;font-weight:500;text-decoration:none;letter-spacing:.2px}
.nav a.is-active::after{content:"";position:absolute;left:0;right:0;top:24px;height:2px;background:var(--purple)}
.hero__title{position:absolute;left:0;top:278px;width:1200px;text-align:center;color:var(--white);font-size:64px;line-height:74px;letter-spacing:1px}
.hero__title span{display:block}
.hero__title .light{font-weight:300}
.hero__title .bold{font-weight:800}
.btn-video{position:absolute;left:511px;top:446px;width:178px;height:48px;border:2px solid var(--orange);border-radius:24px;display:flex;align-items:center;justify-content:center;gap:8px;color:var(--white);font-size:12px;font-weight:700;background:rgba(10,18,40,.6)}
.notch{position:absolute;left:540px;width:120px;height:20px}

/* section headings */
.sec-title{position:absolute;left:0;width:1200px;text-align:center;font-size:44px;font-weight:400;letter-spacing:.5px;color:var(--ink)}
.sec-title b{font-weight:800}

/* sectors */
.sector{position:absolute;width:332px;height:357px;text-align:center;border-radius:26px}
.sector--feature{background:linear-gradient(160deg,#3a7fcb 0%,#2c6cbf 100%);box-shadow:0 10px 30px rgba(49,118,181,.3)}
.sector__icon{position:absolute;left:126px;top:18px;width:80px;height:84px}
.sector__name{position:absolute;left:0;top:140px;width:100%;font-size:16px;font-weight:500;letter-spacing:.3px}
.sector__text{position:absolute;left:46px;top:175px;width:240px;font-size:11.5px;line-height:22px;color:var(--body)}
.sector--feature .sector__name,.sector--feature .sector__text{color:var(--white)}
.btn{position:absolute;height:42px;width:136px;border:2px solid currentColor;border-radius:21px;display:flex;align-items:center;justify-content:center;gap:7px;font-size:11px;font-weight:700;letter-spacing:.2px;background:transparent}
.sector .btn{left:98px;top:288px}
.btn svg{width:12px;height:12px}
.divider{position:absolute;width:1px;top:1238px;height:327px;background:var(--line)}

/* about */
.about-band{position:absolute;left:0;top:1759px;width:1194px;height:534px;background:var(--green);border-radius:0 290px 270px 0}
.photo{position:absolute;border:10px solid var(--white)}
.photo--meeting{left:-20px;top:1670px;width:410px;height:428px;border-radius:0 70px 70px 70px;background:linear-gradient(135deg,#c9bba7 0%,#8d8172 45%,#3b3a40 100%);z-index:2}
.photo--clinic{left:117px;top:1807px;width:373px;height:402px;border-radius:70px;background:linear-gradient(180deg,#e7e3de 0%,#b5b9c2 50%,#4a5f96 100%);z-index:1}
.about__title{position:absolute;left:563px;top:1802px;color:var(--white);font-size:44px;line-height:54px;letter-spacing:.5px}
.about__title .light{font-weight:300}
.about__title .bold{font-weight:700}
.about__text{position:absolute;left:563px;top:1976px;width:495px;color:var(--white);font-size:11.5px;line-height:22.4px}
.btn--ghost-white{color:var(--white)}

/* media */
.media-img{position:absolute;border-radius:18px;box-shadow:0 6px 18px rgba(0,0,0,.12)}
.media-img--handshake{left:154px;top:2517px;width:366px;height:386px;background:linear-gradient(135deg,#ece6dd 0%,#b59d86 45%,#5a4a40 100%)}
.media-img--office{left:680px;top:2989px;width:366px;height:384px;background:linear-gradient(135deg,#e9e6e1 0%,#c9bfb2 40%,#9d6a4c 100%)}
.post{position:absolute;width:470px}
.post__meta{font-size:11px;color:var(--blue);display:flex;align-items:center;gap:6px}
.post__meta .sep{color:#999}
.post__title{margin-top:22px;font-size:16.5px;line-height:29px;font-weight:600;letter-spacing:.2px;color:var(--ink)}
.post__text{margin-top:12px;font-size:11.5px;line-height:21.6px;color:var(--body)}
.post .btn{position:relative;margin-top:36px;color:var(--orange)}

/* global outlook */
.outlook-band{position:absolute;left:0;top:3464px;width:1200px;height:533px;background:var(--purple-band);border-radius:270px 0 0 270px}
.globe-back{position:absolute;left:835px;top:3523px;width:420px;height:417px;border-radius:150px;border:10px solid var(--white);background:linear-gradient(160deg,#2a3560 0%,#151c33 60%,#0a0f1f 100%)}
.globe-front{position:absolute;left:707px;top:3629px;width:403px;height:432px;border-radius:150px;border:10px solid var(--white);background:radial-gradient(circle at 50% 45%,#6a9fd8 0%,#2b5798 40%,#0c1a38 100%)}
.outlook__title{position:absolute;left:182px;top:3558px;color:var(--white);font-size:44px;letter-spacing:.5px}
.outlook__title .light{font-weight:300}
.outlook__title .bold{font-weight:700}
.outlook__text{position:absolute;left:182px;top:3628px;width:500px;color:var(--white);font-size:11.5px;line-height:22.4px}

/* contact */
.contact-bg{position:absolute;left:0;top:4085px;width:1200px;height:600px;background:
  radial-gradient(circle at 90px 260px,rgba(200,206,218,.5),transparent 180px),
  radial-gradient(circle at 1100px 340px,rgba(200,206,218,.5),transparent 200px),
  linear-gradient(180deg,#ffffff 0%,var(--mist) 100%)}
.contact__title{position:absolute;left:0;top:4104px;width:1200px;text-align:center;font-size:44px;line-height:62px;color:var(--ink)}
.contact__title .light{font-weight:300;display:block}
.contact__title .bold{font-weight:800;display:block;font-size:45px}
.field{position:absolute;background:var(--white);border:1px solid #d9dce3;font-size:14px;color:#3a3a40;padding:0 22px;display:flex;align-items:center}
.field--area{align-items:flex-start;padding-top:18px}
.btn--submit{left:532px;top:4555px;color:var(--orange);background:var(--white);width:134px}

/* footer */
.footer{position:absolute;left:0;top:4685px;width:1200px;height:261px;background:
  linear-gradient(180deg,#2a67b8 0%,#2c64ad 100%)}
.footer h4{position:absolute;color:var(--white);font-size:14.5px;font-weight:700;letter-spacing:.3px}
.footer a{position:absolute;color:var(--white);font-size:12px;text-decoration:none}
.social{position:absolute;top:4796px;width:26px;height:26px;border-radius:50%;border:2px solid var(--white)}
.copyright{position:absolute;left:755px;top:4858px;color:var(--white);font-size:11.5px}
</style>
</head>
<body>
<div class="page">

  <!-- Hero -->
  <header class="hero" role="img" aria-label="Night-time photograph of a glowing digital globe with a rising market chart line"></header>
  <div class="hero__panel"></div>
  <div class="brand">HARBOR CREST HOLDINGS</div>
  <nav class="nav">
    <a class="is-active" style="left:179px">HOME</a>
    <a style="left:257px">ABOUT US</a>
    <a style="left:363px">EXPERTISE</a>
    <a style="left:472px">GLOBAL OUTLOOK</a>
    <a style="left:628px">SECTORS</a>
    <a style="left:726px">MANAGEMENT</a>
    <a style="left:860px">MEDIA</a>
    <a style="left:941px">CONTACT US</a>
  </nav>
  <h1 class="hero__title"><span class="light">HARBOR CREST</span><span class="bold">HOLDINGS</span></h1>
  <div class="btn-video">WATCH VIDEO
    <svg width="13" height="13" viewBox="0 0 12 12"><circle cx="6" cy="6" r="6" fill="#fff"/><path d="M4.6 3.4 8.4 6 4.6 8.6z" fill="#0b1634"/></svg>
  </div>
  <svg class="notch" style="top:620px" viewBox="0 0 120 20"><path d="M0 20 C20 20 26 0 44 0 H76 C94 0 100 20 120 20z" fill="#fff"/><path d="M54 6 60 11 66 6" stroke="#aab" stroke-width="1.5" fill="none"/></svg>

  <!-- Sectors -->
  <h2 class="sec-title" style="top:718px">OUR <b>SECTORS</b></h2>

  <div class="sector" style="left:93px;top:835px">
    <svg class="sector__icon" viewBox="0 0 80 84" fill="none" stroke="var(--purple)" stroke-width="2.4"><path d="M8 80V38L40 12l32 26v42z"/><path d="M40 4v8M34 30h12v10H34z"/><path d="M16 48h10v10H16zM54 48h10v10H54zM16 64h10v10H16zM54 64h10v10H54zM33 80V56h14v24"/><path d="M2 80h76"/></svg>
    <div class="sector__name">REAL ESTATE</div>
    <p class="sector__text">Lorem ipsum dolor sit amesectdipiscing elit, sed do eiusmod tempor incididunt ut labore et dolore magnm suspendisse ultrices gravisus commodo viverra</p>
    <div class="btn" style="color:var(--purple)">READ MORE <svg viewBox="0 0 12 12"><circle cx="6" cy="6" r="6" fill="currentColor"/><path d="M5 3.5 7.5 6 5 8.5" stroke="#fff" stroke-width="1.4" fill="none"/></svg></div>
  </div>

  <div class="sector sector--feature" style="left:432px;top:835px">
    <svg class="sector__icon" viewBox="0 0 80 84" fill="none" stroke="#fff" stroke-width="2.4"><rect x="4" y="8" width="72" height="56" rx="4"/><path d="M4 20h72"/><circle cx="12" cy="14" r="1.5"/><circle cx="18" cy="14" r="1.5"/><circle cx="24" cy="14" r="1.5"/><path d="M18 30h6l6 20h26l6-16H28"/><path d="M34 38h22M34 44h20M40 34v16M48 34v16"/><circle cx="34" cy="58" r="4"/><circle cx="54" cy="58" r="4"/></svg>
    <div class="sector__name">E-COMMERCE</div>
    <p class="sector__text">Lorem ipsum dolor sit amesectdipiscing elit, sed do eiusmod tempor incididunt ut labore et dolore magnm suspendisse ultrices gravisus commodo viverra</p>
    <div class="btn" style="color:var(--white)">READ MORE <svg viewBox="0 0 12 12"><circle cx="6" cy="6" r="6" fill="currentColor"/><path d="M5 3.5 7.5 6 5 8.5" stroke="#2f6fc4" stroke-width="1.4" fill="none"/></svg></div>
  </div>

  <div class="sector" style="left:767px;top:835px">
    <svg class="sector__icon" viewBox="0 0 80 84" fill="none" stroke="var(--green)" stroke-width="2.4"><path d="M40 76C14 56 4 44 4 28 4 16 13 8 24 8c7 0 12 4 16 9 4-5 9-9 16-9 11 0 20 8 20 20 0 16-10 28-36 48z"/><path d="M34 28h12v10h10v12H46v10H34V50H24V38h10z"/></svg>
    <div class="sector__name">HEALTHCARE</div>
    <p class="sector__text">Lorem ipsum dolor sit amesectdipiscing elit, sed do eiusmod tempor incididunt ut labore et dolore magnm suspendisse ultrices gravisus commodo viverra</p>
    <div class="btn" style="color:var(--green)">READ MORE <svg viewBox="0 0 12 12"><circle cx="6" cy="6" r="6" fill="currentColor"/><path d="M5 3.5 7.5 6 5 8.5" stroke="#fff" stroke-width="1.4" fill="none"/></svg></div>
  </div>

  <div class="divider" style="left:432px"></div>
  <div class="divider" style="left:764px"></div>

  <div class="sector" style="left:93px;top:1233px">
    <svg class="sector__icon" viewBox="0 0 80 84" fill="none" stroke="var(--orange)" stroke-width="2.4"><rect x="28" y="26" width="24" height="50" rx="6"/><path d="M32 26v-8h16v8M36 18V8h14l6 6"/><path d="M34 44h12M34 52h12"/><path d="M14 14l3 6 6 3-6 3-3 6-3-6-6-3 6-3zM66 40l2 4 4 2-4 2-2 4-2-4-4-2 4-2z"/></svg>
    <div class="sector__name">BEAUTY &amp; PERSONAL CARE</div>
    <p class="sector__text">Lorem ipsum dolor sit amesectdipiscing elit, sed do eiusmod tempor incididunt ut labore et dolore magnm suspendisse ultrices gravisus commodo viverra</p>
    <div class="btn" style="color:var(--orange)">READ MORE <svg viewBox="0 0 12 12"><circle cx="6" cy="6" r="6" fill="currentColor"/><path d="M5 3.5 7.5 6 5 8.5" stroke="#fff" stroke-width="1.4" fill="none"/></svg></div>
  </div>

  <div class="sector" style="left:432px;top:1233px">
    <svg class="sector__icon" viewBox="0 0 80 84" fill="none" stroke="var(--red)" stroke-width="2.4"><rect x="14" y="16" width="52" height="52" rx="3"/><rect x="24" y="26" width="32" height="32"/><path d="M22 6v10M30 6v10M38 6v10M46 6v10M54 6v10M22 68v10M30 68v10M38 68v10M46 68v10M54 68v10M4 26h10M4 34h10M4 42h10M4 50h10M4 58h10M66 26h10M66 34h10M66 42h10M66 50h10M66 58h10"/><path d="M32 34h8v8h8v8"/><circle cx="32" cy="34" r="2"/><circle cx="48" cy="50" r="2"/></svg>
    <div class="sector__name">TECHNOLOGY</div>
    <p class="sector__text">Lorem ipsum dolor sit amesectdipiscing elit, sed do eiusmod tempor incididunt ut labore et dolore magnm suspendisse ultrices gravisus commodo viverra</p>
    <div class="btn" style="color:var(--red)">READ MORE <svg viewBox="0 0 12 12"><circle cx="6" cy="6" r="6" fill="currentColor"/><path d="M5 3.5 7.5 6 5 8.5" stroke="#fff" stroke-width="1.4" fill="none"/></svg></div>
  </div>

  <div class="sector" style="left:767px;top:1233px">
    <svg class="sector__icon" viewBox="0 0 80 84" fill="none" stroke="var(--pink)" stroke-width="2.4"><circle cx="16" cy="16" r="10"/><circle cx="64" cy="16" r="10"/><circle cx="16" cy="68" r="10"/><circle cx="64" cy="68" r="10"/><circle cx="40" cy="42" r="8"/><path d="M40 28v6M40 50v6M26 42h6M48 42h6M26 16h28M26 68h28M16 26v32M64 26v32"/></svg>
    <div class="sector__name">RESOURCES</div>
    <p class="sector__text">Lorem ipsum dolor sit amesectdipiscing elit, sed do eiusmod tempor incididunt ut labore et dolore magnm suspendisse ultrices gravisus commodo viverra</p>
    <div class="btn" style="color:var(--red)">READ MORE <svg viewBox="0 0 12 12"><circle cx="6" cy="6" r="6" fill="currentColor"/><path d="M5 3.5 7.5 6 5 8.5" stroke="#fff" stroke-width="1.4" fill="none"/></svg></div>
  </div>

  <!-- About -->
  <section class="about-band"></section>
  <div class="photo photo--clinic" role="img" aria-label="Photograph of medical staff in scrubs walking along a bright hospital corridor"></div>
  <div class="photo photo--meeting" role="img" aria-label="Photograph of business people reviewing documents at a desk"></div>
  <h2 class="about__title"><span class="light">ABOUT</span><br><span class="bold">HARBOR CREST<br>HOLDINGS</span></h2>
  <p class="about__text">Lorem ipsum dolor sit amet, consectetur adipiscing do eiusmod tempor incididunt ut labore et dolore magna a suspendisse ultrices grav commodo viverra maecenas accumsan lacus vel facilisis. Lorem ipsum dolor sit amet, consectetur adipiscing do eiusmod tempor incididunt ut labore et dolore magna a suspendisse ultrices grav commodo viverra maecenas accumsan lacus vel facilisis. Lorem ipsum dolor sit amet, consectetur adipiscing do eiusmod tempor incididunt ut labore et dolore magna a suspmod tempor incididunt ut labore et dolore magna a suspendisse ultrices grav commodo viverra maeceendisse ultrices grav commodo viverra</p>
  <div class="btn btn--ghost-white" style="left:563px;top:2203px">READ MORE <svg viewBox="0 0 12 12"><circle cx="6" cy="6" r="6" fill="currentColor"/><path d="M5 3.5 7.5 6 5 8.5" stroke="#169d7d" stroke-width="1.4" fill="none"/></svg></div>

  <!-- Media -->
  <h2 class="sec-title" style="top:2390px">OUR <b>MEDIA</b></h2>

  <div class="media-img media-img--handshake" role="img" aria-label="Photograph of a smiling couple shaking hands over a laptop"></div>
  <article class="post" style="left:586px;top:2551px">
    <div class="post__meta"><svg width="11" height="11" viewBox="0 0 11 11"><rect x="0" y="1.5" width="11" height="9.5" rx="1" fill="#3176b5"/><rect x="1.5" y="4" width="8" height="5.5" fill="#fff"/></svg>Dec 15.2020 <span class="sep">|</span> Comments</div>
    <h3 class="post__title">LOREM IPSUM DOLOR SIT AMETON<br>ECTETUR ADIPISCING</h3>
    <p class="post__text">Lorem ipsum dolor sit amet, consectetur adipiscing elit, sed do eiusmod tempor incididunt ut labore et dolore magna aliqua.uis ipsum suspendisse ultrices gravida. Risus commodo viverra maecenas accumsan lacus vel facilisis. Lorem ipsum dolor t dolore magna aliqua.uis ipsum suspendisse cesavidus commodo viverra maet dolore magna aliqs ipsum suspendisse ultricgravida. Risus commodo viverra maesit amet, consectetur adipiscing</p>
    <div class="btn">READ MORE <svg viewBox="0 0 12 12"><circle cx="6" cy="6" r="6" fill="currentColor"/><path d="M5 3.5 7.5 6 5 8.5" stroke="#fff" stroke-width="1.4" fill="none"/></svg></div>
  </article>

  <article class="post" style="left:154px;top:3024px">
    <div class="post__meta"><svg width="11" height="11" viewBox="0 0 11 11"><rect x="0" y="1.5" width="11" height="9.5" rx="1" fill="#3176b5"/><rect x="1.5" y="4" width="8" height="5.5" fill="#fff"/></svg>Dec 15.2020 <span class="sep">|</span> Comments</div>
    <h3 class="post__title">LOREM IPSUM DOLOR SIT AMETON<br>ECTETUR ADIPISCING</h3>
    <p class="post__text">Lorem ipsum dolor sit amet, consectetur adipiscing elit, sed do eiusmod tempor incididunt ut labore et dolore magna aliqua.uis ipsum suspendisse ultrices gravida. Risus commodo viverra maecenas accumsan lacus vel facilisis. Lorem ipsum dolor t dolore magna aliqua.uis ipsum suspendisse cesavidus commodo viverra maet dolore magna aliqs ipsum suspendisse ultricgravida. Risus commodo viverra maesit amet, consectetur adipiscing</p>
    <div class="btn">READ MORE <svg viewBox="0 0 12 12"><circle cx="6" cy="6" r="6" fill="currentColor"/><path d="M5 3.5 7.5 6 5 8.5" stroke="#fff" stroke-width="1.4" fill="none"/></svg></div>
  </article>
  <div class="media-img media-img--office" role="img" aria-label="Photograph of a smiling woman leaning over a laptop in a bright office"></div>

  <!-- Global outlook -->
  <section class="outlook-band"></section>
  <div class="globe-back" role="img" aria-label="Photograph of a man working at a computer in a dim office"></div>
  <div class="globe-front" role="img" aria-label="Illustration of a glowing wireframe globe held above a hand"></div>
  <h2 class="outlook__title"><span class="light">GLOBAL</span> <span class="bold">OUTLOOK</span></h2>
  <p class="outlook__text">Lorem ipsum dolor sit amet, consectetur adipiscing do eiusmod tempor incididunt ut labore et dolore magna a suspendisse ultrices grav commodo viverra maecenas accumsan lacus vel facilisis. Lorem ipsum dolor sit amet, consectetur adipiscing do eiusmod tempor incididunt ut labore et dolore magna a suspendisse ultrices grav commodo viverra maecenas accumsan lacus vel facilisis. Lorem ipsum dolor sit amet, consectetur adipiscing do eiusmod tempor incididunt ut labore et dolore magna a suspmod tempor incididunt ut labore et dolore magna a suspendisse ultrices grav commodo viverra maeceendisse ultrices grav commodo viverra</p>
  <div class="btn btn--ghost-white" style="left:182px;top:3855px">READ MORE <svg viewBox="0 0 12 12"><circle cx="6" cy="6" r="6" fill="currentColor"/><path d="M5 3.5 7.5 6 5 8.5" stroke="#7656a3" stroke-width="1.4" fill="none"/></svg></div>

  <!-- Contact -->
  <div class="contact-bg" role="img" aria-label="Faint background pattern of connected network nodes"></div>
  <h2 class="contact__title"><span class="light">CONTACT</span><span class="bold">HARBOR CREST HOLDINGS</span></h2>
  <div class="field" style="left:232px;top:4278px;width:361px;height:54px">First Name</div>
  <div class="field" style="left:605px;top:4278px;width:361px;height:54px">Last Name</div>
  <div class="field" style="left:232px;top:4343px;width:361px;height:54px">Email address</div>
  <div class="field" style="left:605px;top:4343px;width:361px;height:54px">Phone Number</div>
  <div class="field field--area" style="left:232px;top:4408px;width:734px;height:116px">Message</div>
  <div class="btn btn--submit">SUBMIT <svg viewBox="0 0 12 12"><circle cx="6" cy="6" r="6" fill="currentColor"/><path d="M5 3.5 7.5 6 5 8.5" stroke="#fff" stroke-width="1.4" fill="none"/></svg></div>

  <!-- Footer -->
  <footer class="footer">
    <h4 style="left:144px;top:66px">QUICK LINKS</h4>
    <a style="left:144px;top:112px">Home</a>
    <a style="left:144px;top:139px">About Us</a>
    <a style="left:144px;top:166px">Expertise</a>
    <a style="left:144px;top:193px">Global Outlook</a>
    <a style="left:288px;top:112px">Sectors</a>
    <a style="left:288px;top:139px">Management</a>
    <a style="left:288px;top:166px">Media</a>
    <a style="left:288px;top:193px">Contact Us</a>

    <h4 style="left:453px;top:66px">OUR SECTORS</h4>
    <a style="left:453px;top:112px">Real Estate</a>
    <a style="left:453px;top:139px">E-Commerce</a>
    <a style="left:453px;top:166px">Healthcare</a>
    <a style="left:453px;top:193px">Beauty &amp; Personal Care</a>
    <a style="left:597px;top:112px">Technology</a>
    <a style="left:597px;top:139px">Resources</a>

    <h4 style="left:755px;top:66px">STAY CONNECTED</h4>
  </footer>
  <svg class="notch" style="top:4685px" viewBox="0 0 120 20"><path d="M0 0 C20 0 26 20 44 20 H76 C94 20 100 0 120 0z" fill="#f1f3f7"/><path d="M54 13 60 8 66 13" stroke="#aab" stroke-width="1.5" fill="none"/></svg>
  <span class="social" style="left:755px"></span>
  <span class="social" style="left:799px"></span>
  <span class="social" style="left:848px"></span>
  <span class="social" style="left:897px"></span>
  <p class="copyright">2020 Harbor Crest Holdings All rights reserved.</p>

</div>
</body>
</html>
```